Brand and Marketing Coach Needs PDF Designed

I have content that i need placed into a simple but great PDF design. The PDF is about the formula I use to build personal brands. This is geared towards entrepreneurs, experts, coaches, therapists, wellness practitioners, and indpendent business owners who serve to improve the lives of others.
The company name is changing from TorvelCast to Selling with the Village (I don't have that logo yet, so working backwards a bit. For now, the TorvelCast logo can be used.) My brand is NOT formal and corporate, but it's also not neon-pink and screaming at you. It's down to earth, hip, a bit modern but warm. It's about no BS and authenticity. The final deliverable should make the reader feel focused, smart, motivated and hopeful.

Target Market(s)

Conscious entrepreneurs and small business owners. this one is specifically for pharmacy entrepreneurs but this will be used for various audiences later.

Font styles to use
Sans Serif

Colors
eaf1f7
3377b5
6b449b
f37122
faa54b
f68e4e
ffc214

Requirements
Must have
• Modern design. colors that match logo - 4e5583 (i think that is the blue.) d65a40.
• Could have these colors as well: c6a254, 01bcc3
• But open to other colors
Nice to have
• I'd like to see some ways to make this PDF simple and readable, and eye-catching. I'd also like to use the uploaded ebooks for design ideas.
Should not have
• neon colors, clip art

```html
<!DOCTYPE html>
<html lang="en">
<head>
<meta charset="utf-8">
<title>The Personal Brand Formula – For Pharmacy Entrepreneurs</title>
<link rel="stylesheet" href="https://fonts.googleapis.com/css2?family=Rajdhani:wght@300;400;500&display=swap">
<style>
  :root {
    --purple: #6a429a;
    --orange: #f56f1c;
    --ink: #1a1a1a;
    --amp-grey: #c4c4c4;
    --brand-navy: #4e5583;
    --white: #ffffff;
    --photo-light: #f2f2f2;
    --photo-mid: #b9b9b9;
    --photo-dark: #4a4a4a;
  }
  * { box-sizing: border-box; margin: 0; padding: 0; }
  html, body { width: 1200px; height: 927px; overflow: hidden; background: var(--white); }
  body { font-family: "Rajdhani", sans-serif; }

  .cover { position: relative; width: 1200px; height: 927px; overflow: hidden; }

  .hero {
    position: absolute; left: 0; top: 0; width: 1200px; height: 456px;
    background:
      radial-gradient(ellipse 260px 330px at 390px 260px, var(--photo-dark), transparent 75%),
      linear-gradient(90deg, var(--photo-mid) 0%, #d8d8d8 35%, var(--photo-light) 60%, var(--white) 100%);
  }

  .headline {
    position: absolute; left: 695px; top: 82px;
    font-weight: 300; color: var(--ink); line-height: 1;
  }
  .headline .line-1 { display: block; font-size: 84px; letter-spacing: 1px; }
  .headline .line-2 { display: block; font-size: 68px; margin-top: -6px; }
  .headline .line-2 b { font-weight: 500; }
  .headline .tail { position: relative; display: block; margin-top: -4px; padding-left: 74px; }
  .headline .amp {
    position: absolute; left: 6px; top: 6px;
    font-size: 112px; color: var(--amp-grey); font-weight: 300; line-height: 1;
  }
  .headline .line-3, .headline .line-4 { position: relative; display: block; font-size: 54px; line-height: 0.86; }
  .headline .line-4 { margin-left: 8px; }

  .brand-name {
    position: absolute; left: 922px; top: 365px;
    display: flex; align-items: center; gap: 6px;
    font-family: "Rajdhani", sans-serif; font-weight: 500; font-size: 34px;
    color: var(--brand-navy);
  }
  .brand-name .dot { width: 40px; height: 40px; border-radius: 50%; background: var(--brand-navy); }

  .title-panel {
    position: absolute; left: 0; top: 456px; width: 1200px; height: 471px;
    background: var(--purple); color: var(--white);
  }
  .title {
    position: absolute; left: 174px; top: 125px;
    font-weight: 300; font-size: 70px; letter-spacing: 1px; line-height: 1;
  }
  .audience-tag { position: absolute; left: 174px; top: 204px; width: 442px; height: 40px; }
  .audience-tag svg { position: absolute; inset: 0; }
  .audience-tag span {
    position: relative; display: block; padding-left: 12px;
    font-weight: 300; font-size: 30px; line-height: 40px; color: var(--white);
  }
  .summary {
    position: absolute; left: 174px; top: 298px;
    font-weight: 400; font-size: 20px; letter-spacing: 0.3px;
  }
</style>
</head>
<body>
<main class="cover">
  <section class="hero" role="img" aria-label="Black and white portrait of the coach seated on stone steps, wearing a blazer and jeans, looking to the side"></section>

  <h2 class="headline">
    <span class="line-1">Step it up,</span>
    <span class="line-2">get noticed<b>,</b></span>
    <span class="tail">
      <span class="amp">&amp;</span>
      <span class="line-3">grow your</span>
      <span class="line-4">client base</span>
    </span>
  </h2>

  <div class="brand-name"><span class="dot"></span>TorvelCast</div>

  <section class="title-panel">
    <h1 class="title">The Personal Brand Formula</h1>
    <div class="audience-tag">
      <svg width="442" height="40" viewBox="0 0 442 40" aria-hidden="true">
        <polygon points="0,0 442,0 406,40 0,40" fill="var(--orange)"/>
      </svg>
      <span>For Pharmacy Entrepreneurs</span>
    </div>
    <p class="summary">The quick n' dirty guide to creating a unique personal brand that attracts your ideal clients.</p>
  </section>
</main>
</body>
</html>
```